Maplecrest Disability - Social Security Disability Attorneys

Our company is expanding to attract clients nationwide for our social security disability practice. We have a logo, but I am looking for a creative and elegant letterhead that projects an image of being technologically advanced but still professional enough for the legal field. I am looking for the "wow factor" combined with this is still professional enough for a law practice.

Requesting letterhead and business card design
Updates

Had to update and change the logo. The previous logo had a typo. Please send updates with the new logo for consideration. The letterhead and business cards should be professional enough to be used for a law firm. Thanks.

Industry/Entity Type

Law Practice, Law Firm, Healthcare Industry, Government

Colors

Designer to choose colors to be used in the design.

Requirements
Nice to have
• **Please create a vertical design for the business card**

```html
<!DOCTYPE html>
<html lang="en">
<head>
<meta charset="utf-8">
<title>Maplecrest Disability – Letterhead</title>
<link rel="stylesheet" href="https://fonts.googleapis.com/css2?family=Cormorant+Garamond:wght@600&family=Open+Sans:wght@600&display=swap">
<style>
  :root {
    --backdrop: #d9dcde;
    --paper: #ffffff;
    --brand-blue: #1f4fc4;
    --edge-blue: #3a86e0;
    --accent-orange: #f07a1a;
    --ink-grey: #5a5a5a;
    --rule-grey: #9a9a9a;
  }
  * { margin: 0; padding: 0; box-sizing: border-box; }
  html, body {
    width: 1200px; height: 784px; overflow: hidden;
    background: var(--backdrop);
  }
  .stage {
    width: 1200px; height: 784px;
    display: flex; align-items: center; justify-content: center;
  }
  .letterhead {
    position: relative;
    width: 524px; height: 740px;
    background: var(--paper);
    box-shadow: 0 6px 18px rgba(0,0,0,0.12);
    overflow: hidden;
  }
  .edge-top {
    position: absolute; top: 0; left: 0; right: 0; height: 5px;
    background: var(--accent-orange);
  }
  .edge-bottom {
    position: absolute; bottom: 0; left: 0; right: 0; height: 6px;
    background: var(--edge-blue);
  }
  .brand {
    position: absolute; top: 48px; right: 40px;
    text-align: right;
    font-family: "Cormorant Garamond", Georgia, serif;
    font-weight: 600;
    color: var(--brand-blue);
  }
  .brand-name {
    display: flex; align-items: center; justify-content: flex-end; gap: 8px;
    font-size: 21px; letter-spacing: 1.5px; text-transform: uppercase;
  }
  .brand-dot {
    width: 9px; height: 9px; border-radius: 50%;
    background: var(--brand-blue);
  }
  .brand-tagline {
    margin-top: 3px;
    font-size: 7.5px; letter-spacing: 2px; text-transform: uppercase;
  }
  .contact {
    position: absolute; left: 0; right: 0; bottom: 24px;
    font-family: "Open Sans", Arial, sans-serif;
    font-weight: 600;
    text-align: center;
  }
  .contact-address {
    display: flex; align-items: center; justify-content: center; gap: 10px;
    font-size: 8.5px; color: var(--accent-orange);
  }
  .contact-address .rule {
    width: 44px; height: 1px; background: var(--rule-grey);
  }
  .contact-icons {
    display: flex; justify-content: center; gap: 9px;
    margin: 8px 0 7px;
  }
  .contact-icons svg { width: 12px; height: 12px; }
  .contact-lines {
    font-size: 8.5px; color: var(--ink-grey);
  }
  .contact-lines .sep { color: var(--accent-orange); margin: 0 4px; }
</style>
</head>
<body>
<main class="stage">
  <article class="letterhead">
    <div class="edge-top"></div>

    <header class="brand">
      <div class="brand-name"><span>Maplecrest Disability</span><span class="brand-dot"></span></div>
      <div class="brand-tagline">Social Security Disability Attorneys</div>
    </header>

    <footer class="contact">
      <div class="contact-address">
        <span class="rule"></span>
        <span>1200 Sample Road, Ste 210, California, 90000, United States</span>
        <span class="rule"></span>
      </div>
      <div class="contact-icons">
        <svg viewBox="0 0 12 12" aria-label="Address"><circle cx="6" cy="6" r="6" fill="#f07a1a"/><path d="M6 2.5a2 2 0 0 0-2 2c0 1.6 2 4.5 2 4.5s2-2.9 2-4.5a2 2 0 0 0-2-2z" fill="#fff"/></svg>
        <svg viewBox="0 0 12 12" aria-label="Phone"><circle cx="6" cy="6" r="6" fill="#f07a1a"/><path d="M4 3l1.2 1.6-.6.7c.4.9 1.1 1.6 2 2l.7-.6L9 8l-.6 1C6 9 3 6 3 3.6z" fill="#fff"/></svg>
        <svg viewBox="0 0 12 12" aria-label="Mobile"><circle cx="6" cy="6" r="6" fill="#f07a1a"/><rect x="4.2" y="2.6" width="3.6" height="6.8" rx=".6" fill="#fff"/></svg>
        <svg viewBox="0 0 12 12" aria-label="Email"><circle cx="6" cy="6" r="6" fill="#f07a1a"/><rect x="3" y="4" width="6" height="4.2" fill="#fff"/><path d="M3 4l3 2.3L9 4" stroke="#f07a1a" stroke-width=".7" fill="none"/></svg>
        <svg viewBox="0 0 12 12" aria-label="Website"><circle cx="6" cy="6" r="6" fill="#f07a1a"/><circle cx="6" cy="6" r="3" fill="none" stroke="#fff" stroke-width=".8"/><path d="M3 6h6M6 3c-1.4 1.7-1.4 4.3 0 6M6 3c1.4 1.7 1.4 4.3 0 6" stroke="#fff" stroke-width=".7" fill="none"/></svg>
      </div>
      <div class="contact-lines">
        (000) 000-0000<span class="sep">|</span>(000) 000-0000<span class="sep">|</span>info@maplecrestdisability.com<span class="sep">|</span>www.maplecrestdisability.com
      </div>
    </footer>

    <div class="edge-bottom"></div>
  </article>
</main>
</body>
</html>
```